Im open to ideas.. I was thinking on my business cards aswell as my logo. a place for my name. email. phone number and abn..

ive attched a file with my business logo. which i dont love the colours.. i was think a dark background with charcoal letters so something along those colour schumes but im open to ideas..

BRM Constructions

```html
<!DOCTYPE html>
<html lang="en">
<head>
<meta charset="UTF-8">
<title>BRM Constructions – Business Card</title>
<link href="https://fonts.googleapis.com/css2?family=Raleway:wght@400;500;600&display=swap" rel="stylesheet">
<style>
  :root {
    --page-bg: #e9e6e1;
    --card-white: #f7f7f5;
    --red-light: #ee2a33;
    --red-dark: #c8141d;
    --ink: #1d1d1f;
    --charcoal: #2f2f31;
    --paper-text: #ffffff;
  }
  html, body {
    margin: 0;
    width: 1200px;
    height: 1022px;
    overflow: hidden;
    background: var(--page-bg);
    font-family: "Raleway", sans-serif;
  }
  .card {
    position: absolute;
    left: 140px;
    top: 248px;
    width: 920px;
    height: 526px;
    border-radius: 22px;
    overflow: hidden;
    display: flex;
    box-shadow: 0 18px 40px rgba(0,0,0,0.18);
  }
  .brand-panel {
    width: 410px;
    background: var(--card-white);
    display: flex;
    align-items: center;
    justify-content: center;
    gap: 14px;
  }
  .brand-mark {
    width: 22px;
    height: 22px;
    background: var(--red-light);
  }
  .brand-name {
    font-weight: 600;
    font-size: 30px;
    color: var(--charcoal);
    letter-spacing: 0.5px;
  }
  .divider {
    position: relative;
    width: 4px;
    background: var(--ink);
  }
  .divider svg {
    position: absolute;
    left: -2px;
    top: 72px;
  }
  .details-panel {
    flex: 1;
    background: linear-gradient(135deg, var(--red-light) 0%, var(--red-dark) 100%);
    padding: 70px 0 0 44px;
    color: var(--paper-text);
  }
  .person-name {
    margin: 0;
    font-weight: 500;
    font-size: 34px;
    letter-spacing: 1.5px;
    text-transform: uppercase;
  }
  .person-role {
    margin: 4px 0 0;
    font-size: 20px;
    color: var(--ink);
  }
  .abn {
    margin: 12px 0 0;
    font-size: 20px;
    color: var(--ink);
  }
  .abn strong { font-weight: 600; }
  .contact-list {
    list-style: none;
    margin: 22px 0 0;
    padding: 0;
  }
  .contact-list li {
    display: flex;
    align-items: center;
    gap: 14px;
    font-size: 20px;
    line-height: 34px;
  }
  .contact-list svg { flex: none; }
</style>
</head>
<body>
  <div class="card">
    <div class="brand-panel">
      <span class="brand-mark"></span>
      <span class="brand-name">BRM Constructions</span>
    </div>
    <div class="divider">
      <svg width="20" height="22" viewBox="0 0 20 22" aria-hidden="true">
        <polygon points="0,0 18,11 0,22" fill="#f7f7f5"/>
      </svg>
    </div>
    <div class="details-panel">
      <h1 class="person-name">Daniel Morris</h1>
      <p class="person-role">Director</p>
      <p class="abn"><strong>ABN</strong>: 41 208 635 117</p>
      <ul class="contact-list">
        <li>
          <svg width="16" height="16" viewBox="0 0 16 16" aria-hidden="true">
            <path d="M3 1l3 3-1.5 2c1 2 3 4 5 5L11.5 9.5l3 3L13 15C7 15 1 9 1 3z" fill="#1d1d1f"/>
          </svg>
          +330 2460-1184
        </li>
        <li>
          <svg width="16" height="16" viewBox="0 0 16 16" aria-hidden="true">
            <rect x="1" y="3" width="14" height="10" fill="none" stroke="#1d1d1f" stroke-width="1.6"/>
            <path d="M1 3l7 6 7-6" fill="none" stroke="#1d1d1f" stroke-width="1.6"/>
          </svg>
          info@brmconstructions.com
        </li>
        <li>
          <svg width="16" height="16" viewBox="0 0 16 16" aria-hidden="true">
            <circle cx="8" cy="8" r="7" fill="#1d1d1f"/>
            <path d="M1 8h14M8 1c-3 3-3 11 0 14M8 1c3 3 3 11 0 14" stroke="#ee2a33" stroke-width="1" fill="none"/>
          </svg>
          www.brmconstructions.com
        </li>
      </ul>
    </div>
  </div>
</body>
</html>
```